Website and Mobile Devices design for food related application.

We need a design that is simple yet playful. The design should be food related if possible.
This design will be on the website and the mobile platform markets we intend application to be deployed too.
This application/website is called "Forkwizo[.com]. Its a random restaurant picker for the indecisive users.
Updates
Hi all, I picked a design. Again lots of great designs were submitted but I picked one that was more in line with what I wanted.
Target Market(s)
young internet savvy users.
Industry/Entity Type
Restaurant
Look and feel
Each slider illustrates characteristics of the customer's brand and the style your logo design should communicate.

```html
<!DOCTYPE html>
<html lang="en">
<head>
<meta charset="utf-8">
<title>Forkwizo – app screens</title>
<link href="https://fonts.googleapis.com/css2?family=Arimo:wght@400;700&display=swap" rel="stylesheet">
<style>
:root{
  --stage:#cdd8dd;
  --bar-black:#0c0c0c;
  --accent:#d81d1d;
  --list-top:#36a7c7;
  --list-mid:#4cc2d4;
  --list-bottom:#3a86c9;
  --white:#ffffff;
  --tab-text:#cfcfcf;
  --map-light:#eeebe2;
  --map-mid:#e6e0cc;
  --map-warm:#ece0b0;
  --map-green:#d9e4c6;
}
*{box-sizing:border-box;margin:0;padding:0}
html,body{width:1200px;height:1000px;overflow:hidden}
body{background:var(--stage);font-family:"Arimo",Helvetica,Arial,sans-serif;position:relative}
.icons{position:absolute;width:0;height:0}
.screen{position:absolute;top:355px;width:285px;height:423px;background:var(--bar-black);overflow:hidden;display:flex;flex-direction:column}
.screen--list{left:45px}
.screen--map{left:455px}
.screen--favourites{left:868px}

.status-bar{height:18px;flex:none;display:flex;align-items:center;justify-content:space-between;padding:0 6px;color:var(--white);font-size:10px;font-weight:700;background:linear-gradient(#222,#050505)}
.status-bar .carrier{display:flex;align-items:flex-end;gap:3px}
.signal{display:flex;align-items:flex-end;gap:1px}
.signal i{display:block;width:2px;background:var(--white)}
.status-bar .time{font-size:12px}
.battery{width:18px;height:8px;border:1px solid var(--white);border-radius:1px;padding:1px}
.battery span{display:block;height:100%;background:var(--white)}

.search-bar{height:37px;flex:none;display:flex;align-items:center;gap:6px;padding:0 6px;background:linear-gradient(#5a5a5a,#2d2d2d)}
.search-bar .side-icon{width:16px;height:16px;color:#ddd;flex:none}
.search-field{flex:1;height:23px;border-radius:12px;background:linear-gradient(#fff,#ececec);display:flex;align-items:center;padding:0 4px 0 6px;gap:4px;box-shadow:inset 0 1px 2px rgba(0,0,0,.5)}
.search-field svg{width:13px;height:13px;color:#555;flex:none}
.search-field .divider{width:1px;height:16px;background:#bbb}
.search-field .query{flex:1;font-size:11px;color:#111}
.book-button{width:24px;height:16px;border-radius:8px;background:var(--accent);display:flex;align-items:center;justify-content:center}
.book-button svg{width:14px;height:10px;color:var(--white)}

.sort-control{height:28px;flex:none;display:flex;justify-content:center;align-items:center;background:#2a2a2a;padding:0 15px}
.sort-control span{flex:1;height:24px;display:flex;align-items:center;justify-content:center;color:var(--white);font-size:11px;background:linear-gradient(#6a6a6a,#3c3c3c);border-right:1px solid #222}
.sort-control span.is-active{background:linear-gradient(#a32424,#6b1111)}

.content{flex:1;position:relative;overflow:hidden}
.restaurant-list{background:linear-gradient(170deg,var(--list-top),var(--list-mid) 45%,var(--list-bottom));list-style:none;height:100%}
.restaurant{height:53px;position:relative;border-bottom:1px solid rgba(255,255,255,.25)}
.restaurant .dot{position:absolute;left:10px;top:14px;width:18px;height:18px;border-radius:50%;background:rgba(255,255,255,.45);display:flex;align-items:center;justify-content:center}
.restaurant .dot::after{content:"";width:9px;height:9px;border-radius:50%;background:var(--accent)}
.restaurant .name{position:absolute;left:58px;top:14px;color:var(--white);font-size:11.5px;white-space:nowrap}
.restaurant .meta{position:absolute;left:58px;top:28px;font-size:7.5px;font-weight:700;color:var(--accent);width:150px;white-space:nowrap}
.meta .price{position:absolute;left:67px}
.meta .distance{position:absolute;left:108px}
.restaurant .chevron{position:absolute;right:8px;top:16px;width:10px;height:16px;color:var(--accent)}

.map-area{height:100%;background:
  radial-gradient(ellipse 55% 40% at 40% 62%,var(--map-green),transparent 70%),
  radial-gradient(ellipse 60% 50% at 80% 80%,var(--map-warm),transparent 70%),
  linear-gradient(160deg,var(--map-light),var(--map-mid))}

.tab-bar{height:40px;flex:none;display:flex;background:linear-gradient(#3a3a3a,#111);padding:0 4px}
.tab{flex:1;display:flex;flex-direction:column;align-items:center;justify-content:flex-end;padding-bottom:3px;color:var(--tab-text);font-size:8px;gap:2px;white-space:nowrap}
.tab svg{width:16px;height:16px;color:#eee}
.tab.is-active{background:rgba(255,255,255,.12);color:var(--accent);font-weight:700}
</style>
</head>
<body>

<svg class="icons" aria-hidden="true">
  <defs>
    <symbol id="i-pin" viewBox="0 0 16 16"><path d="M8 1a5 5 0 0 0-5 5c0 4 5 9 5 9s5-5 5-9a5 5 0 0 0-5-5zm0 7a2 2 0 1 1 0-4 2 2 0 0 1 0 4z" fill="currentColor"/></symbol>
    <symbol id="i-pushpin" viewBox="0 0 16 16"><path d="M6 2h5l-1 4 3 3H9l-2 6-1-6H3l3-3z" fill="currentColor"/></symbol>
    <symbol id="i-star" viewBox="0 0 16 16"><path d="M8 1l2.2 4.6 5 .6-3.7 3.4 1 5L8 12.2 3.5 14.6l1-5L.8 6.2l5-.6z" fill="currentColor"/></symbol>
    <symbol id="i-card" viewBox="0 0 16 16"><rect x="1" y="3" width="14" height="10" rx="1" fill="none" stroke="currentColor" stroke-width="1.5"/><rect x="1" y="5.5" width="14" height="2" fill="currentColor"/></symbol>
    <symbol id="i-phone" viewBox="0 0 16 16"><path d="M4 1l3 3-1.5 2a8 8 0 0 0 4.5 4.5L12 9l3 3-2 2.5C7 14 2 9 1.5 3z" fill="currentColor"/></symbol>
    <symbol id="i-search" viewBox="0 0 16 16"><circle cx="6.5" cy="6.5" r="4.5" fill="none" stroke="currentColor" stroke-width="2"/><path d="M10 10l5 5" stroke="currentColor" stroke-width="2.4"/></symbol>
    <symbol id="i-refresh" viewBox="0 0 16 16"><path d="M13 6A5.5 5.5 0 0 0 3 5M3 10a5.5 5.5 0 0 0 10 1" fill="none" stroke="currentColor" stroke-width="1.8"/><path d="M13 1v5H8zM3 15v-5h5z" fill="currentColor"/></symbol>
    <symbol id="i-locate" viewBox="0 0 16 16"><circle cx="8" cy="8" r="6.5" fill="none" stroke="currentColor" stroke-width="1.5"/><path d="M8 3l2 7-2-1.5L6 10z" fill="currentColor"/></symbol>
    <symbol id="i-book" viewBox="0 0 14 10"><path d="M1 1h5l1 1 1-1h5v8H8l-1 1-1-1H1z" fill="none" stroke="currentColor" stroke-width="1.3"/><path d="M7 2v7" stroke="currentColor" stroke-width="1"/></symbol>
    <symbol id="i-chevron" viewBox="0 0 10 16"><path d="M1 1l8 7-8 7" fill="none" stroke="currentColor" stroke-width="2"/></symbol>
  </defs>
</svg>

<section class="screen screen--list">
  <div class="status-bar"><span class="carrier"><span class="signal"><i style="height:3px"></i><i style="height:5px"></i><i style="height:7px"></i><i style="height:9px"></i></span>Mobile</span><span class="time">6:40 PM</span><span class="battery"><span></span></span></div>
  <div class="search-bar"><svg class="side-icon"><use href="#i-refresh"/></svg><div class="search-field"><svg><use href="#i-search"/></svg><span class="divider"></span><span class="query">Forkwizo</span><span class="book-button"><svg><use href="#i-book"/></svg></span></div></div>
  <div class="sort-control"><span class="is-active">Distance</span><span>Cuisine</span><span>Random</span></div>
  <div class="content">
    <ul class="restaurant-list">
      <li class="restaurant"><span class="dot"></span><span class="name">Name Of Restaurant 1</span><span class="meta">Chinese<span class="price">$</span><span class="distance">99m</span></span><svg class="chevron"><use href="#i-chevron"/></svg></li>
      <li class="restaurant"><span class="dot"></span><span class="name">Name Of Restaurant 2</span><span class="meta">French<span class="price">$$$</span><span class="distance">120m</span></span><svg class="chevron"><use href="#i-chevron"/></svg></li>
      <li class="restaurant"><span class="dot"></span><span class="name">Name Of Restaurant 3</span><span class="meta">British<span class="price">$$</span><span class="distance">200m</span></span><svg class="chevron"><use href="#i-chevron"/></svg></li>
      <li class="restaurant"><span class="dot"></span><span class="name">Name Of Restaurant 4</span><span class="meta">Moroccan<span class="price">$$</span><span class="distance">200m</span></span><svg class="chevron"><use href="#i-chevron"/></svg></li>
      <li class="restaurant"><span class="dot"></span><span class="name">Name Of Restaurant 5</span><span class="meta">Japanese<span class="price">$$$</span><span class="distance">99m</span></span><svg class="chevron"><use href="#i-chevron"/></svg></li>
      <li class="restaurant"><span class="dot"></span><span class="name">Name Of Restaurant 6</span><span class="meta">American<span class="price">$</span><span class="distance">99m</span></span><svg class="chevron"><use href="#i-chevron"/></svg></li>
    </ul>
  </div>
  <nav class="tab-bar">
    <span class="tab is-active"><svg><use href="#i-pin"/></svg>Stations</span>
    <span class="tab"><svg><use href="#i-pushpin"/></svg>Map</span>
    <span class="tab"><svg><use href="#i-star"/></svg>Favoris</span>
    <span class="tab"><svg><use href="#i-card"/></svg>Reservation</span>
    <span class="tab"><svg><use href="#i-phone"/></svg>Contact</span>
  </nav>
</section>

<section class="screen screen--map">
  <div class="status-bar"><span class="carrier"><span class="signal"><i style="height:3px"></i><i style="height:5px"></i><i style="height:7px"></i><i style="height:9px"></i></span>Mobile</span><span class="time">6:40 PM</span><span class="battery"><span></span></span></div>
  <div class="search-bar"><svg class="side-icon"><use href="#i-locate"/></svg><div class="search-field"><svg><use href="#i-search"/></svg><span class="divider"></span><span class="query">Forkwizo</span><span class="book-button"><svg><use href="#i-book"/></svg></span></div></div>
  <div class="sort-control"><span class="is-active">Distance</span><span>Cuisine</span><span>Random</span></div>
  <div class="content">
    <div class="map-area" role="img" aria-label="Detailed city street map with lettered red markers showing nearby restaurants"></div>
  </div>
  <nav class="tab-bar">
    <span class="tab"><svg><use href="#i-pin"/></svg>Stations</span>
    <span class="tab is-active"><svg><use href="#i-pushpin"/></svg>Map</span>
    <span class="tab"><svg><use href="#i-star"/></svg>Favoris</span>
    <span class="tab"><svg><use href="#i-card"/></svg>Reservation</span>
    <span class="tab"><svg><use href="#i-phone"/></svg>Contact</span>
  </nav>
</section>

<section class="screen screen--favourites">
  <div class="status-bar"><span class="carrier"><span class="signal"><i style="height:3px"></i><i style="height:5px"></i><i style="height:7px"></i><i style="height:9px"></i></span>Mobile</span><span class="time">6:40 PM</span><span class="battery"><span></span></span></div>
  <div class="search-bar"><svg class="side-icon"><use href="#i-refresh"/></svg><div class="search-field"><svg><use href="#i-search"/></svg><span class="divider"></span><span class="query">Forkwizo</span></div></div>
  <div class="sort-control"><span class="is-active">Distance</span><span>Cuisine</span><span>Random</span></div>
  <div class="content">
    <ul class="restaurant-list">
      <li class="restaurant"><span class="dot"></span><span class="name">Name Of Restaurant 1</span><span class="meta">Chinese<span class="price">$</span><span class="distance">99m</span></span><svg class="chevron"><use href="#i-chevron"/></svg></li>
      <li class="restaurant"><span class="dot"></span><span class="name">Name Of Restaurant 2</span><span class="meta">French<span class="price">$$$</span><span class="distance">120m</span></span><svg class="chevron"><use href="#i-chevron"/></svg></li>
      <li class="restaurant"><span class="dot"></span><span class="name">Name Of Restaurant 3</span><span class="meta">British<span class="price">$$</span><span class="distance">200m</span></span><svg class="chevron"><use href="#i-chevron"/></svg></li>
    </ul>
  </div>
  <nav class="tab-bar">
    <span class="tab"><svg><use href="#i-pin"/></svg>Stations</span>
    <span class="tab"><svg><use href="#i-pushpin"/></svg>Map</span>
    <span class="tab is-active"><svg><use href="#i-star"/></svg>Favoris</span>
    <span class="tab"><svg><use href="#i-card"/></svg>Reservation</span>
    <span class="tab"><svg><use href="#i-phone"/></svg>Contact</span>
  </nav>
</section>

</body>
</html>
```